Residential Remodeling Contractor needs updated business card

I need a new design for my business card.
Name of the company is Ridgefell Construction. I need a card that commands presence, strength, integrity. I have been in business for 28 years. I am a Residential Remodeling Contractor that covers all aspects of a residential remodel and build.

```html
<!DOCTYPE html>
<html lang="en">
<head>
<meta charset="utf-8">
<title>Ridgefell Construction – Business Card</title>
<link href="https://fonts.googleapis.com/css2?family=Montserrat:wght@400;500;600;700&display=swap" rel="stylesheet">
<style>
  :root {
    --brand-blue: #1f3c7e;
    --brand-blue-deep: #18316a;
    --paper: #ffffff;
    --backdrop: #d9d8d6;
    --ink-light: #ffffff;
  }
  * { margin: 0; padding: 0; box-sizing: border-box; }
  html, body {
    width: 1200px; height: 801px; overflow: hidden;
    background: var(--backdrop);
    font-family: "Montserrat", sans-serif;
  }
  .stage {
    position: relative; width: 1200px; height: 801px;
    display: flex; align-items: center; justify-content: center; gap: 40px;
  }
  .card {
    position: relative; width: 540px; height: 309px; overflow: hidden;
    box-shadow: 0 10px 24px rgba(0,0,0,.18);
  }

  /* Front */
  .card-front { background: var(--paper); }
  .front-panel {
    position: absolute; left: 150px; right: 0; background: var(--brand-blue);
  }
  .tagline-band { top: 80px; height: 50px; }
  .info-band { top: 134px; bottom: 0; }
  .brand-name {
    position: absolute; left: 160px; top: 24px;
    font-weight: 600; font-size: 20px; line-height: 1.15;
    letter-spacing: .06em; text-transform: uppercase;
    color: var(--brand-blue);
  }
  .tagline {
    position: absolute; left: 180px; top: 97px;
    color: var(--ink-light); font-weight: 500; font-size: 13px;
    letter-spacing: .09em; text-transform: uppercase;
  }
  .person { position: absolute; left: 190px; top: 160px; color: var(--ink-light); }
  .person-name { font-weight: 700; font-size: 19px; letter-spacing: .04em; text-transform: uppercase; }
  .person-role { font-size: 11px; margin-top: 2px; }
  .contact-list {
    position: absolute; left: 190px; top: 222px; list-style: none;
    color: var(--ink-light); font-size: 11.5px; line-height: 1.55;
  }
  .contact-list li { display: flex; align-items: center; gap: 7px; }
  .contact-list svg { width: 11px; height: 11px; flex: none; }
  .address {
    position: absolute; right: 28px; top: 150px; text-align: left;
    color: var(--ink-light); font-size: 11.5px; line-height: 1.5;
  }

  /* Back */
  .card-back {
    background: var(--brand-blue);
    display: flex; align-items: center; justify-content: center;
  }
  .back-name {
    color: var(--brand-blue-deep); font-weight: 600; font-size: 26px;
    letter-spacing: .06em; text-transform: uppercase; text-align: center; line-height: 1.2;
  }
</style>
</head>
<body>
<main class="stage">
  <section class="card card-front" aria-label="Business card front">
    <div class="front-panel tagline-band"></div>
    <div class="front-panel info-band"></div>
    <p class="brand-name">Ridgefell<br>Construction</p>
    <p class="tagline">I have been in business for 28 years</p>
    <div class="person">
      <p class="person-name">Marcus Delane</p>
      <p class="person-role">Director</p>
    </div>
    <ul class="contact-list">
      <li>
        <svg viewBox="0 0 12 12" aria-hidden="true"><path d="M3 1 L5 3.5 L4 5 Q5 7 7 8 L8.5 7 L11 9 L10 11 Q5 11 1 3 Z" fill="#fff"/></svg>
        (555) 214-0387
      </li>
      <li>
        <svg viewBox="0 0 12 12" aria-hidden="true"><rect x="1" y="2.5" width="10" height="7" fill="none" stroke="#fff" stroke-width="1.2"/><path d="M1 3 L6 7 L11 3" fill="none" stroke="#fff" stroke-width="1.2"/></svg>
        info@ridgefellbuild.com
      </li>
      <li>
        <svg viewBox="0 0 12 12" aria-hidden="true"><circle cx="6" cy="6" r="5" fill="none" stroke="#fff" stroke-width="1.1"/><ellipse cx="6" cy="6" rx="2.2" ry="5" fill="none" stroke="#fff" stroke-width="1"/><path d="M1 6 H11" stroke="#fff" stroke-width="1"/></svg>
        www.ridgefellbuild.com
      </li>
    </ul>
    <p class="address">742 Alder Lane<br>Millbrook, GA 30999</p>
  </section>

  <section class="card card-back" aria-label="Business card back">
    <p class="back-name">Ridgefell<br>Construction</p>
  </section>
</main>
</body>
</html>
```